American cannabis tech company business card design

Pavrel.com is seeking a modern, professional, and brand-aligned business card that represents our company and its core values: Mission, Story, Values, and Impact. As an innovative cannabis company, we want a business card that is not only visually appealing but also serves as a representation of who we are and what we stand for.

Project Scope: Design a double-sided business card that integrates our brand identity and core values. Incorporate our key brand elements, ensuring a sleek and contemporary aesthetic. Visually reflect our core values (Mission, Story, Values, Impact) in a way that is engaging yet professional.

Target Market(s)

Vendors, third parties,

Contact Information for Business Card

Contact details (name, title, email, phone, website, etc.)

Font styles to use
Other font styles liked:
• Caslon, Centra

Colors

Designer to choose colors to be used in the design.

Requirements
Must have
• Pavrel.com logo and branding A creative yet clean way to integrate our core values (Mission, Story, Values, Impact) Modern typography and a well-structured layout
Nice to have
• forest green, grey, white, black
Should not have
• references to marijuana, leafs, plants, or related product

```html
<!DOCTYPE html>
<html lang="en">
<head>
<meta charset="utf-8">
<title>Pavrel.com Business Card</title>
<link href="https://fonts.googleapis.com/css2?family=Arimo:wght@400;700&family=Libre+Caslon+Text:wght@700&display=swap" rel="stylesheet">
<style>
  :root {
    --bg: #1b1d1f;
    --forest-deep: #0f2414;
    --forest: #17421e;
    --forest-mid: #1e5a26;
    --forest-bright: #2f8a35;
    --leaf-faint: #2c5a33;
    --white: #ffffff;
    --white-soft: rgba(255,255,255,.78);
  }
  * { box-sizing: border-box; margin: 0; padding: 0; }
  html, body { width: 1200px; height: 840px; overflow: hidden; background: var(--bg); }
  .canvas { position: relative; width: 1200px; height: 840px; }

  .card {
    position: absolute;
    width: 600px;
    height: 345px;
    border-radius: 22px;
    overflow: hidden;
    box-shadow: 0 14px 34px rgba(0,0,0,.55);
  }

  .brand-name {
    position: absolute;
    font-family: "Libre Caslon Text", serif;
    font-weight: 700;
    color: var(--white);
    letter-spacing: 1px;
    line-height: 1;
  }

  .core-values {
    position: absolute;
    font-family: "Arimo", sans-serif;
    font-weight: 400;
    color: var(--white-soft);
    letter-spacing: 3px;
    text-transform: uppercase;
    white-space: nowrap;
  }
  .core-values .dot { padding: 0 6px; }

  /* Front */
  .card-front { left: 60px; top: 70px; }
  .front-pattern {
    position: absolute; inset: 0;
    background: linear-gradient(110deg, var(--forest-deep) 0%, var(--forest) 45%, var(--forest-mid) 70%, var(--forest-bright) 100%);
  }
  .card-front .brand-name {
    left: 0; right: 0; top: 130px;
    text-align: center;
    font-size: 74px;
  }
  .card-front .core-values {
    left: 0; right: 0; top: 226px;
    text-align: center;
    font-size: 13px;
  }

  /* Back */
  .card-back {
    left: 540px; top: 435px;
    background: linear-gradient(120deg, var(--forest-deep) 0%, var(--forest) 55%, var(--forest-mid) 100%);
    font-family: "Arimo", sans-serif;
    color: var(--white);
  }
  .card-back .brand-name { left: 36px; top: 112px; font-size: 64px; }
  .back-emblem {
    position: absolute; right: 40px; top: 70px;
    width: 230px; height: 230px; border-radius: 50%;
    background: radial-gradient(circle, var(--leaf-faint) 0%, rgba(44,90,51,.55) 55%, rgba(44,90,51,0) 72%);
  }
  .holder {
    position: absolute; right: 34px; top: 30px;
    text-align: right;
  }
  .holder-name { font-weight: 700; font-size: 19px; letter-spacing: .5px; }
  .holder-title { font-size: 14px; margin-top: 3px; }
  .holder-bar {
    position: absolute; right: 0; top: 24px;
    width: 8px; height: 50px; background: var(--white);
  }
  .card-back .core-values {
    right: 34px; bottom: 38px;
    text-align: right;
    font-size: 10px;
    letter-spacing: 2px;
    line-height: 1.7;
  }
  .contact {
    position: absolute; left: 40px; bottom: 34px;
    font-size: 15px; line-height: 1.35;
  }
  .address { margin-bottom: 14px; }
  .contact-list { list-style: none; }
  .contact-list li { display: flex; align-items: center; gap: 8px; }
  .contact-list svg { width: 14px; height: 14px; flex: none; }
</style>
</head>
<body>
<div class="canvas">

  <section class="card card-front">
    <div class="front-pattern" role="img" aria-label="Repeating decorative pattern in dark to bright forest green"></div>
    <div class="brand-name">PAVREL</div>
    <div class="core-values">Mission<span class="dot">·</span>Story<span class="dot">·</span>Values<span class="dot">·</span>Impact</div>
  </section>

  <section class="card card-back">
    <div class="back-emblem" role="img" aria-label="Large faint decorative emblem in muted green"></div>
    <div class="brand-name">PAVREL</div>

    <div class="holder">
      <div class="holder-name">DANIEL HART</div>
      <div class="holder-title">Managing Director</div>
    </div>
    <div class="holder-bar"></div>

    <div class="core-values">Mission<br>Story<br>Values<br>Impact</div>

    <div class="contact">
      <div class="address">Your Address<br>City, State, Zip 0000</div>
      <ul class="contact-list">
        <li>
          <svg viewBox="0 0 24 24" fill="#fff"><path d="M6.6 10.8a15.1 15.1 0 0 0 6.6 6.6l2.2-2.2a1 1 0 0 1 1-.25 11.4 11.4 0 0 0 3.6.57 1 1 0 0 1 1 1V20a1 1 0 0 1-1 1A17 17 0 0 1 3 4a1 1 0 0 1 1-1h3.5a1 1 0 0 1 1 1c0 1.25.2 2.45.57 3.57a1 1 0 0 1-.25 1z"/></svg>
          044-555 210 348
        </li>
        <li>
          <svg viewBox="0 0 24 24" fill="#fff"><path d="M3 5h18v14H3z M3 5l9 7 9-7" stroke="#17421e" stroke-width="1.5"/></svg>
          info@pavrel.com
        </li>
        <li>
          <svg viewBox="0 0 24 24"><circle cx="12" cy="12" r="10" fill="#fff"/><path d="M2 12h20M12 2c3 3 3 17 0 20M12 2c-3 3-3 17 0 20" stroke="#17421e" stroke-width="1.5" fill="none"/></svg>
          www.pavrel.com
        </li>
      </ul>
    </div>
  </section>

</div>
</body>
</html>
```